Harborline Auto LLC

Car Dealer Customer Service
Address: 2874 Cresthaven Road, Shelbyville, TN 37162
web: www.harborlineautoxq.net
email: harborlineautoxq@mailnest.example
Phone: (931) 555-0148
Phone: (629) 555-0173

```html
<!DOCTYPE html>
<html lang="en">
<head>
<meta charset="utf-8">
<title>Harborline Auto – Business Card</title>
<link href="https://fonts.googleapis.com/css2?family=Montserrat:wght@400;500;800&display=swap" rel="stylesheet">
<style>
  :root {
    --stage: #333333;
    --brand-blue: #1e7bad;
    --ink-blue: #1a73a8;
    --band-blue: #2a92cc;
    --band-yellow: #ebb142;
    --paper: #ffffff;
    --ink: #151515;
  }
  * { box-sizing: border-box; margin: 0; padding: 0; }
  html, body {
    width: 1200px; height: 984px; overflow: hidden;
    background: var(--stage);
    font-family: "Montserrat", sans-serif;
  }
  .card {
    position: absolute; left: 220px;
    width: 760px; height: 434px;
    overflow: hidden;
  }
  /* Front side */
  .card--front { top: 50px; background: var(--brand-blue); }
  .front-mark {
    position: absolute; left: 50%; top: 62px;
    width: 180px; height: 180px; margin-left: -90px;
    border-radius: 50%; background: var(--paper); opacity: .95;
  }
  .front-name {
    position: absolute; left: 0; right: 0; top: 272px;
    text-align: center; color: var(--paper);
    font-weight: 800; font-size: 46px; letter-spacing: 2px;
  }
  /* Back side */
  .card--back { top: 500px; background: var(--paper); }
  .back-mark {
    position: absolute; left: 115px; top: 60px;
    width: 150px; height: 150px; border-radius: 50%;
    background: var(--band-blue);
  }
  .back-name {
    position: absolute; left: 20px; width: 360px; top: 232px;
    text-align: center; color: var(--ink-blue);
    font-weight: 800; font-size: 30px; letter-spacing: 1px;
  }
  .divider {
    position: absolute; left: 398px; top: 70px;
    width: 2px; height: 262px; background: var(--band-blue);
  }
  .contact {
    position: absolute; left: 424px; top: 72px; width: 320px;
    color: var(--ink); font-weight: 500;
  }
  .contact__role { font-size: 19px; margin-bottom: 14px; }
  .contact__address { font-size: 18px; line-height: 1.3; margin-bottom: 14px; }
  .contact__line {
    display: flex; align-items: center; gap: 8px;
    font-size: 17px; margin-bottom: 8px; white-space: nowrap;
  }
  .contact__line--small { font-size: 15px; }
  .contact__icon { width: 18px; height: 18px; flex: none; }
  .web-domain { color: var(--band-blue); }
  .bands { position: absolute; left: 0; bottom: 0; width: 760px; height: 34px; }
</style>
</head>
<body>
  <section class="card card--front">
    <div class="front-mark"></div>
    <div class="front-name">HARBORLINE AUTO</div>
  </section>

  <section class="card card--back">
    <div class="back-mark"></div>
    <div class="back-name">HARBORLINE AUTO</div>
    <div class="divider"></div>
    <div class="contact">
      <p class="contact__role">Car Dealer Customer Service</p>
      <p class="contact__address">2874 Cresthaven Road,<br>Shelbyville, TN 37162</p>
      <p class="contact__line">
        <svg class="contact__icon" viewBox="0 0 24 24"><path fill="#1e7bad" d="M6.6 10.8a15 15 0 0 0 6.6 6.6l2.2-2.2a1 1 0 0 1 1-.25 11.4 11.4 0 0 0 3.6.6 1 1 0 0 1 1 1V20a1 1 0 0 1-1 1A17 17 0 0 1 3 4a1 1 0 0 1 1-1h3.5a1 1 0 0 1 1 1c0 1.25.2 2.45.6 3.6a1 1 0 0 1-.25 1z"/></svg>
        (931) 555-0148
      </p>
      <p class="contact__line">
        <svg class="contact__icon" viewBox="0 0 24 24"><path fill="#1e7bad" d="M3 8c0-2 4-3 9-3s9 1 9 3v2h-5V8H8v2H3zM6 11h12l2 8H4zM10 13h4v4h-4z"/></svg>
        (629) 555-0173
      </p>
      <p class="contact__line contact__line--small">
        <svg class="contact__icon" viewBox="0 0 24 24"><rect x="2" y="5" width="20" height="14" fill="#1e7bad"/><path d="M2 5l10 8 10-8" fill="none" stroke="#fff" stroke-width="1.6"/></svg>
        harborlineautoxq@mailnest.example
      </p>
      <p class="contact__line">
        <svg class="contact__icon" viewBox="0 0 24 24"><circle cx="12" cy="12" r="10" fill="#1e7bad"/><path d="M2 12h20M12 2c3 3 3 17 0 20M12 2c-3 3-3 17 0 20" fill="none" stroke="#fff" stroke-width="1.3"/></svg>
        <span>www.<span class="web-domain">harborlineautoxq</span>.net</span>
      </p>
    </div>
    <svg class="bands" viewBox="0 0 760 34" preserveAspectRatio="none">
      <polygon points="0,0 345,0 318,34 0,34" fill="#ebb142"/>
      <polygon points="360,0 760,0 760,34 333,34" fill="#2a92cc"/>
    </svg>
  </section>
</body>
</html>
```